Moxy Fen needs some awesome stationary

Do you have what it takes to get my brand? You either do or you don't, have a crack at a design and you my just win my business.

I don't want to waste your or my time, so put your creative genius on either a business card or envelope.

I however need a package of stationary that follows the same brand. I will message you to complete the remaining should I like your first submission.

Here is what I need, have a go!

Basically I need the following for my small business based in melbourne.
- Letterhead (printer ready and MS Word)
- Business Card
- Compliments Slip
- Envelope
- Proposal Cover Page (MS Word only)
- Presentation Folder
- Marbled Fox Cards
- Student Name Tent
- Index Cards
- Vell-Ka

I am establishing the brand and it must be modern, professional but also relaxed; that is not formal and not corporate. It represents a company are leaders, but small enough to care and operate like a bunch of friends. We are bringing people and conversations back to business, and turfing out all the bureaucracy and crazy and wasteful procedures. Its about "lets talk and figure it out together and find even better ways".

Target Market(s)

Mainly companies that build software products, but Agile practices are used in many other industries (even graphic design projects)

Industry/Entity Type

Information Technology

Font styles to use
Sans Serif

Colors
3176b5
aaaaaa

Requirements
Must have
• I like curves and circles and not boxes or rectangles.
• I want a colour rich design with my brand colours, but it must be balanced.
• I want more modern than traditional, but simple modern
Should not have
• Not corporate
• Please don't waste my time if your not going to think about it.
• Don't mess with my primary logo
• Don't change my colours
• Don't overlay logo on image

```html
<!DOCTYPE html>
<html lang="en">
<head>
<meta charset="utf-8">
<title>Moxy Fen – Business Card</title>
<link rel="stylesheet" href="https://fonts.googleapis.com/css2?family=Open+Sans:wght@400;600;700&display=swap">
<style>
  :root {
    --brand-blue: #3176b5;
    --brand-blue-deep: #2458a0;
    --brand-grey: #aaaaaa;
    --rule-grey: #c4c4c4;
    --ink: #333333;
    --card-white: #f7f7f7;
    --backdrop: #e8e8e8;
    --white: #ffffff;
  }
  * { box-sizing: border-box; margin: 0; padding: 0; }
  html, body {
    width: 1200px; height: 800px; overflow: hidden;
    background: var(--backdrop);
    font-family: "Open Sans", Arial, sans-serif;
    color: var(--ink);
  }
  .stage { position: relative; width: 1200px; height: 800px; }

  .card {
    position: absolute;
    top: 248px;
    width: 429px; height: 279px;
    box-shadow: 0 10px 22px rgba(0,0,0,0.18), 0 2px 4px rgba(0,0,0,0.12);
  }
  .card--front { left: 112px; background: var(--card-white); }
  .card--back {
    left: 651px;
    background: radial-gradient(circle at 50% 45%, #3a72bd 0%, var(--brand-blue-deep) 75%);
  }

  /* front */
  .brand {
    position: absolute; left: 64px; top: 32px;
    display: flex; align-items: center; gap: 12px;
  }
  .brand__dot {
    width: 44px; height: 44px; border-radius: 50%;
    background: var(--brand-grey);
  }
  .brand__name {
    font-size: 43px; font-weight: 600; line-height: 1;
    color: var(--brand-blue); letter-spacing: 0.2px;
  }

  .person { position: absolute; left: 38px; top: 124px; }
  .person__name { font-size: 17px; font-weight: 400; color: var(--brand-blue); }
  .person__role { font-size: 10.5px; font-weight: 700; margin-top: 4px; color: var(--ink); }

  .contact {
    position: absolute; left: 222px; top: 110px;
    list-style: none; font-size: 13.5px; line-height: 18.5px; color: var(--ink);
  }
  .contact__item { display: flex; gap: 8px; }
  .contact__icon { width: 11px; height: 11px; flex: none; margin-top: 4px; }

  .divider {
    position: absolute; left: 21px; top: 213px; width: 380px;
    height: 2px; background: var(--rule-grey);
  }
  .footer {
    position: absolute; left: 38px; top: 222px;
    font-size: 10.5px; line-height: 15px; color: var(--ink);
  }
  .footer__company { font-weight: 700; color: var(--brand-blue); }
  .footer strong { font-weight: 700; }

  /* back */
  .back-brand {
    position: absolute; left: 0; right: 0; top: 82px;
    display: flex; justify-content: center; align-items: center; gap: 12px;
  }
  .back-brand__dot {
    width: 48px; height: 48px; border-radius: 50%; background: var(--white);
  }
  .back-brand__name {
    font-size: 40px; font-weight: 600; color: var(--white); line-height: 1;
  }
  .back-url {
    position: absolute; left: 0; right: 0; top: 196px;
    text-align: center; font-size: 16.5px; color: var(--white); letter-spacing: 0.2px;
  }
</style>
</head>
<body>
<main class="stage">
  <section class="card card--front" aria-label="Business card front">
    <div class="brand">
      <span class="brand__dot"></span>
      <span class="brand__name">Moxy Fen</span>
    </div>

    <div class="person">
      <p class="person__name">Dana Keller</p>
      <p class="person__role">CEO, Professional Scrum Trainer</p>
    </div>

    <ul class="contact">
      <li class="contact__item">
        <svg class="contact__icon" viewBox="0 0 12 12" aria-hidden="true">
          <path d="M6 0.5a4 4 0 0 0-4 4c0 3 4 7 4 7s4-4 4-7a4 4 0 0 0-4-4z" fill="#3176b5"/>
          <circle cx="6" cy="4.5" r="1.4" fill="#f7f7f7"/>
        </svg>
        <span>PO Box 4410, Harlow Park,<br>VIC 3199, Australia</span>
      </li>
      <li class="contact__item">
        <svg class="contact__icon" viewBox="0 0 12 12" aria-hidden="true">
          <circle cx="6" cy="6" r="5.5" fill="#3176b5"/>
          <rect x="3" y="4" width="6" height="4" fill="none" stroke="#f7f7f7" stroke-width="0.9"/>
          <path d="M3 4l3 2.2L9 4" fill="none" stroke="#f7f7f7" stroke-width="0.9"/>
        </svg>
        <span>dana@moxyfen.com.au</span>
      </li>
      <li class="contact__item">
        <svg class="contact__icon" viewBox="0 0 12 12" aria-hidden="true">
          <path d="M2.5 0.8l2 2.3-1.1 1.4c0.7 1.6 2 2.9 3.6 3.6l1.4-1.1 2.3 2-1.2 2.2C5.4 11 1 6.6 0.8 2z" fill="#3176b5"/>
        </svg>
        <span>+61 400 127 386</span>
      </li>
    </ul>

    <div class="divider"></div>

    <div class="footer">
      <p class="footer__company">Moxy Fen Pty Ltd</p>
      <p>PO Box 4410, Harlow Park, VIC 3199, Australia</p>
      <p>ABN 42 905 318 274 &nbsp;| Phone <strong>1300MOXYF</strong> | www.moxyfen.com.au</p>
    </div>
  </section>

  <section class="card card--back" aria-label="Business card back">
    <div class="back-brand">
      <span class="back-brand__dot"></span>
      <span class="back-brand__name">Moxy Fen</span>
    </div>
    <p class="back-url">www.moxyfen.com.au</p>
  </section>
</main>
</body>
</html>
```